TALMORK

The business want a professional looking business card. We have a scetch we will add but want the extra upgrade, and would like more suggestions for variations of our business cards.

```html
<!DOCTYPE html>
<html lang="en">
<head>
<meta charset="UTF-8">
<title>TALMORK Business Card</title>
<link rel="stylesheet" href="https://fonts.googleapis.com/css2?family=Montserrat:wght@400;500;700&display=swap">
<style>
  :root {
    --backdrop: #1c1c1d;
    --card: #151516;
    --card-edge: #232325;
    --gold: #d9a94a;
    --gold-soft: #b98c3a;
    --ink-light: #f2f2f2;
    --emboss: #2a2a2c;
  }
  html, body {
    margin: 0;
    padding: 0;
    width: 1200px;
    height: 801px;
    overflow: hidden;
    background: var(--backdrop);
    font-family: "Montserrat", sans-serif;
  }
  .sheet {
    width: 1200px;
    height: 801px;
    display: flex;
    align-items: center;
    justify-content: center;
    gap: 40px;
  }
  .card {
    position: relative;
    width: 540px;
    height: 309px;
    border-radius: 18px;
    background: linear-gradient(145deg, var(--card-edge), var(--card) 60%);
    box-shadow: 0 18px 40px rgba(0,0,0,0.55);
    overflow: hidden;
  }
  /* Front */
  .brand {
    position: absolute;
    top: 62px;
    left: 0;
    right: 0;
    display: flex;
    align-items: center;
    justify-content: center;
    gap: 12px;
  }
  .brand-dot {
    width: 14px;
    height: 14px;
    border-radius: 50%;
    background: var(--gold);
  }
  .brand-name {
    color: var(--gold);
    font-weight: 500;
    font-size: 30px;
    letter-spacing: 8px;
  }
  .details {
    position: absolute;
    left: 0;
    right: 0;
    bottom: 58px;
    display: flex;
    align-items: center;
    justify-content: center;
  }
  .person {
    text-align: right;
    padding-right: 20px;
  }
  .person-name {
    color: var(--gold);
    font-weight: 700;
    font-size: 19px;
    margin: 0 0 4px;
  }
  .person-role {
    color: var(--ink-light);
    font-weight: 400;
    font-size: 14px;
    margin: 0;
  }
  .divider {
    width: 1px;
    height: 74px;
    background: var(--gold-soft);
  }
  .contacts {
    list-style: none;
    margin: 0;
    padding: 0 0 0 20px;
    display: flex;
    flex-direction: column;
    gap: 7px;
  }
  .contacts li {
    display: flex;
    align-items: center;
    gap: 8px;
    color: var(--ink-light);
    font-size: 12.5px;
    font-weight: 400;
  }
  .contacts svg {
    width: 12px;
    height: 12px;
    flex: none;
  }
  /* Back */
  .card-back .brand-back {
    position: absolute;
    inset: 0;
    display: flex;
    align-items: center;
    justify-content: center;
    gap: 14px;
  }
  .card-back .brand-dot { background: var(--emboss); width: 18px; height: 18px; }
  .card-back .brand-name {
    color: var(--emboss);
    font-size: 40px;
    letter-spacing: 10px;
  }
</style>
</head>
<body>
<main class="sheet">
  <section class="card card-front" aria-label="Business card front">
    <div class="brand">
      <span class="brand-dot"></span>
      <span class="brand-name">TALMORK</span>
    </div>
    <div class="details">
      <div class="person">
        <p class="person-name">Lars Henrik Vollan</p>
        <p class="person-role">CEO &amp; Founder</p>
      </div>
      <div class="divider"></div>
      <ul class="contacts">
        <li>
          <svg viewBox="0 0 24 24" aria-hidden="true"><path fill="#d9a94a" d="M6.6 10.8a15 15 0 0 0 6.6 6.6l2.2-2.2a1 1 0 0 1 1-.25 11.4 11.4 0 0 0 3.6.57 1 1 0 0 1 1 1V20a1 1 0 0 1-1 1A17 17 0 0 1 3 4a1 1 0 0 1 1-1h3.5a1 1 0 0 1 1 1c0 1.25.2 2.45.57 3.57a1 1 0 0 1-.25 1z"/></svg>
          004791234567
        </li>
        <li>
          <svg viewBox="0 0 24 24" aria-hidden="true"><path fill="#d9a94a" d="M3 5h18a1 1 0 0 1 1 1v12a1 1 0 0 1-1 1H3a1 1 0 0 1-1-1V6a1 1 0 0 1 1-1zm9 7 8-5H4z"/></svg>
          talmork.llc@mailbox.com
        </li>
        <li>
          <svg viewBox="0 0 24 24" aria-hidden="true"><circle cx="12" cy="12" r="9" fill="none" stroke="#d9a94a" stroke-width="2.4"/><path d="M3 12h18M12 3c3 3 3 15 0 18M12 3c-3 3-3 15 0 18" fill="none" stroke="#d9a94a" stroke-width="1.6"/></svg>
          www.talmork.llc
        </li>
      </ul>
    </div>
  </section>

  <section class="card card-back" aria-label="Business card back">
    <div class="brand-back">
      <span class="brand-dot"></span>
      <span class="brand-name">TALMORK</span>
    </div>
  </section>
</main>
</body>
</html>
```